Briloran Clear Springs needs a new business card design (we produce and sell pure bottled water)

We need a clean modern design for our new business cards, We have an existing logo which ultimately cannot be changed, however it could be slighty improved and the colours adjusted. We have this existing logo on all of our bottles, vehicles etc.

Our company slogan is "Pure down to the last drop".
Along with our relevant company information
(Address, phone, website email etc) we will only be using names and not putting position titles for flexibilty.

We are looking for a clean, minimalist modern design.

You can view our website (if need of an update also!) to see our business.

Industry/Entity Type

Business

Contact Information for Business Card

Staff Name : XXXXXX XXXXXX
Address : 9/41 Tavenor St
Halden Rise QLD 4172
Staff Mobile Number : 04XX XXX XXX
Office Phone Number : 07 3918 2457
Staff Email Address : XXXX@brilorancleargo.com.au
Website : www.brilorancleargo.com.au

Font styles to use
Sans Serif

Colors
cee9f5
33a6d7
0492cd
0455a3
3276b5
85abd2
cedeed

Requirements
Must have
• The ability to edit and change the staff members details as we will need to edit for each respective staff member (7 in total)

```html
<!DOCTYPE html>
<html lang="en">
<head>
<meta charset="utf-8">
<title>Briloran Clear Springs – Business Card</title>
<link rel="stylesheet" href="https://fonts.googleapis.com/css2?family=Source+Sans+3:wght@400;600;700&display=swap">
<style>
  :root {
    --brand-blue: #0492cd;
    --brand-sky: #33a6d7;
    --brand-ice: #cee9f5;
    --brand-navy: #0455a3;
    --card-white: #ffffff;
    --ink: #1d1d1d;
    --stage: #e9edf0;
  }
  * { box-sizing: border-box; margin: 0; padding: 0; }
  html, body { width: 1200px; height: 900px; overflow: hidden; }
  body {
    position: relative;
    background: var(--stage);
    font-family: "Source Sans 3", sans-serif;
  }
  .card {
    position: absolute;
    background: var(--card-white);
    overflow: hidden;
    box-shadow: 0 6px 18px rgba(0,0,0,0.12);
  }

  /* Front */
  .card-front { left: 77px; top: 35px; width: 589px; height: 363px; }
  .brand-name {
    position: absolute; left: 33px; top: 88px;
    display: flex; align-items: center; gap: 12px;
    color: var(--brand-blue);
    font-weight: 700; font-size: 30px; line-height: 1.0;
    text-transform: uppercase; letter-spacing: 0.5px;
  }
  .brand-dot {
    width: 22px; height: 22px; border-radius: 50%;
    background: var(--brand-blue); flex: none;
  }
  .bottle-photo {
    position: absolute; left: 452px; top: 28px; width: 68px; height: 146px;
    border-radius: 14px 14px 8px 8px;
    background: linear-gradient(180deg, #bfe3f5 0%, #7cc3e8 55%, #e6f4fb 100%);
  }
  .front-band {
    position: absolute; left: 0; top: 201px; width: 100%; height: 162px;
    background: var(--brand-blue); color: var(--card-white);
  }
  .staff-name {
    position: absolute; left: 33px; top: 22px;
    font-size: 21px; font-weight: 600;
  }
  .contact-list {
    position: absolute; left: 33px; top: 64px; list-style: none;
    font-size: 16px; line-height: 23px;
  }
  .contact-list li { display: flex; align-items: center; gap: 12px; }
  .contact-list svg { width: 11px; height: 11px; fill: var(--card-white); flex: none; }
  .address {
    position: absolute; right: 37px; top: 64px; text-align: right;
    font-size: 16px; line-height: 23px;
  }

  /* Back */
  .card-back { left: 388px; top: 505px; width: 567px; height: 352px; }
  .back-band {
    position: absolute; left: 0; top: 110px; width: 100%; height: 131px;
    background: var(--brand-blue);
  }
  .back-badge {
    position: absolute; left: 165px; top: 98px; width: 240px; height: 155px;
    border-radius: 50%; background: var(--card-white);
    display: flex; align-items: center; justify-content: center;
    color: var(--brand-blue); font-weight: 700; font-size: 25px;
    text-transform: uppercase; text-align: center; line-height: 1.05;
  }
  .website {
    position: absolute; left: 0; top: 264px; width: 100%; text-align: center;
    font-size: 15px; color: var(--ink); font-weight: 600;
  }
</style>
</head>
<body>

<section class="card card-front">
  <div class="brand-name"><span class="brand-dot"></span><span>Briloran<br>Clear Springs</span></div>
  <div class="bottle-photo" role="img" aria-label="Photo of a large bottled water cooler jug"></div>
  <div class="front-band">
    <p class="staff-name">Marcus Delaney</p>
    <ul class="contact-list">
      <li><svg viewBox="0 0 10 10"><path d="M2.5 0h5a1 1 0 0 1 1 1v8a1 1 0 0 1-1 1h-5a1 1 0 0 1-1-1V1a1 1 0 0 1 1-1zm0 1.5v6h5v-6z"/></svg>0400 218 639</li>
      <li><svg viewBox="0 0 10 10"><path d="M2 0.5l2 2-1 1.3c.6 1.3 1.6 2.3 2.9 2.9L7.2 5.7l2.3 2-1.3 1.8C4.2 9.4 0.5 5.8 0.4 1.8z"/></svg>07 3918 2457</li>
      <li><svg viewBox="0 0 10 10"><path d="M0 2h10v6H0zM0 2l5 3.5L10 2v1.2L5 6.7 0 3.2z" fill-rule="evenodd"/></svg>info@brilorancleargo.com.au</li>
    </ul>
    <p class="address">9/41 Tavenor St<br>Halden Rise QLD 4172</p>
  </div>
</section>

<section class="card card-back">
  <div class="back-band"></div>
  <div class="back-badge">Briloran<br>Clear Springs</div>
  <p class="website">www.brilorancleargo.com.au</p>
</section>

</body>
</html>
```